Business Card Design Project

We need a business card for a new technology services company. We develop software and implement software packages for our business customers and although we will begin with just one or two service offerings, our service offerings will expand over time. Our name comes from the an author, KL Barrow, and his "idea" was that opportunity should be based on ability and achievement, not on social status.

We would like to see a design that is standard in its size and shape, but stands apart in its dramatic color contrasts. The card should not use too many colors - the colors used in the background should highlight the brilliant blues of the logo (see attachment) to dramatic effect. The background should not be white.

If necessary, you can change the color of the words "KL Barrow", but not the word "Idea".

Card size should be U.S. standard 2 inches by 3.5 inches and provide for 1/8 inch bleed area on each side.

We need a design for both sides of the business card, one side communicating the company logo and contact information, the other side being purely graphical, incorporating the logo but no other information.

Contact Information Required:
Kate Brook
KateBrook@klbarrowvista.com
614-387-2259

Target Market(s)

Business executives

Industry/Entity Type

Software

Requirements
Must have
• It must have the full company logo on one side, and at least the graphic element of the logo on the other. Either that or the full logo on both.
Nice to have
• It would be nice to have a design that could work without needing two different textures. For example, it would be nice if the entire card could be shiny, not just parts of the card.

It would also be nice if texture is something we could add later.
Should not have
• The card should not use the color green.

```html
<!DOCTYPE html>
<html lang="en">
<head>
<meta charset="utf-8">
<title>Barrow Vista – Business Card</title>
<link rel="stylesheet" href="https://fonts.googleapis.com/css2?family=Open+Sans:wght@400;700&display=swap">
<style>
  :root {
    --page: #dcd9d5;
    --card-dark: #1f1f1f;
    --card-mid: #2e2e2e;
    --brand-blue: #1c9fdc;
    --brand-blue-deep: #0d7fbf;
    --rule-grey: #8a8a8a;
    --wordmark-grey: #c4c4c4;
    --text-light: #f2f2f2;
  }
  * { box-sizing: border-box; margin: 0; padding: 0; }
  html, body {
    width: 1200px;
    height: 750px;
    overflow: hidden;
  }
  body {
    background: var(--page);
    font-family: "Open Sans", Arial, sans-serif;
    display: flex;
    align-items: center;
    justify-content: center;
    gap: 50px;
  }
  .card {
    position: relative;
    width: 540px;
    height: 309px;
    border-radius: 20px;
    overflow: hidden;
    box-shadow: 0 10px 24px rgba(0,0,0,0.25);
  }
  .card-surface {
    position: absolute;
    inset: 0;
    background: radial-gradient(ellipse at 45% 40%, var(--card-mid) 0%, var(--card-dark) 75%);
  }
  .wordmark {
    position: absolute;
    font-family: "Open Sans", Arial, sans-serif;
    font-weight: 400;
    color: var(--wordmark-grey);
    letter-spacing: -1px;
    white-space: nowrap;
    line-height: 1;
  }
  /* Front */
  .card-front .wordmark {
    left: 36px;
    top: 122px;
    font-size: 40px;
  }
  .brand-dot {
    position: absolute;
    left: 290px;
    top: 120px;
    width: 40px;
    height: 40px;
    border-radius: 50%;
    background: var(--brand-blue);
  }
  .name-band {
    position: absolute;
    left: 0;
    right: 0;
    top: 176px;
    height: 40px;
    background: linear-gradient(180deg, var(--brand-blue) 0%, var(--brand-blue-deep) 100%);
    border-top: 2px solid var(--rule-grey);
    border-bottom: 2px solid var(--rule-grey);
    display: flex;
    align-items: center;
    justify-content: center;
  }
  .person-name {
    color: var(--text-light);
    font-weight: 700;
    font-size: 19px;
    letter-spacing: 0.5px;
    text-transform: uppercase;
  }
  .contact-row {
    position: absolute;
    left: 0;
    right: 0;
    top: 240px;
    display: flex;
    justify-content: center;
    align-items: center;
    gap: 14px;
    color: var(--text-light);
    font-size: 12.5px;
  }
  .contact-item {
    display: flex;
    align-items: center;
    gap: 6px;
  }
  .contact-item svg { width: 12px; height: 12px; fill: var(--text-light); }
  .contact-divider {
    width: 1px;
    height: 26px;
    background: var(--rule-grey);
  }
  /* Back */
  .back-dot {
    position: absolute;
    left: 30px;
    top: 70px;
    width: 165px;
    height: 165px;
    border-radius: 50%;
    background: var(--brand-blue);
    opacity: 0.3;
  }
  .card-back .wordmark {
    right: 34px;
    top: 128px;
    font-size: 50px;
  }
</style>
</head>
<body>

  <section class="card card-front" aria-label="Business card front">
    <div class="card-surface" role="img" aria-label="Dark charcoal card surface with subtle tonal pattern"></div>
    <div class="wordmark">Barrow Vista</div>
    <div class="brand-dot"></div>
    <div class="name-band">
      <span class="person-name">Kate Brook</span>
    </div>
    <div class="contact-row">
      <span class="contact-item">
        <svg viewBox="0 0 24 24" aria-hidden="true"><path d="M6.6 10.8a15.1 15.1 0 0 0 6.6 6.6l2.2-2.2c.3-.3.7-.4 1-.2 1.1.4 2.3.6 3.6.6.6 0 1 .4 1 1V20c0 .6-.4 1-1 1A17 17 0 0 1 3 4c0-.6.4-1 1-1h3.5c.6 0 1 .4 1 1 0 1.3.2 2.5.6 3.6.1.3 0 .7-.2 1z"/></svg>
        614-387-2259
      </span>
      <span class="contact-divider"></span>
      <span class="contact-item">
        <svg viewBox="0 0 24 24" aria-hidden="true"><path d="M2 5h20v14H2z M4 7v.5l8 5 8-5V7z" fill-rule="evenodd"/></svg>
        KateBrook@klbarrowvista.com
      </span>
    </div>
  </section>

  <section class="card card-back" aria-label="Business card back">
    <div class="card-surface" role="img" aria-label="Dark charcoal card surface with subtle tonal pattern"></div>
    <div class="back-dot"></div>
    <div class="wordmark">Barrow Vista</div>
  </section>

</body>
</html>
```